BUSINESS CARD FOR GUITAR SCHOOL

I would like to design a business card for my Guitar Music School. The school is called "Pluck & Lantern".

The card should be yellow.

Target Market(s)

18-35 years old

Industry/Entity Type

School

Contact Information for Business Card

I would like to design a business card for my Guitar Music School. The school is called "Pluck & Lantern". The card should be yellow.

Card must be consistent with my website design: www.pluckandlantern.com.sg

Requirements
Must have
• 1) Name of Company
• 2) Company Logo
• 3) Name of Employee
• 4) Position of Employee
• 5) Contact Number
• 6) Address
Nice to have
• Creative Design
• Card must be consistent with my website design: www.pluckandlantern.com.sg
Should not have
• Boring Design

```html
<!DOCTYPE html>
<html lang="en">
<head>
<meta charset="utf-8">
<title>Pluck &amp; Lantern – Business Card</title>
<link rel="stylesheet" href="https://fonts.googleapis.com/css2?family=Open+Sans:wght@600;800&family=Oswald:wght@300;400&display=swap">
<style>
  :root {
    --card-yellow: #f4d01c;
    --ink: #231f20;
    --muted-grey: #8c8c8c;
    --paper: #ffffff;
    --canvas: #f2f2f2;
    --lettering-grey: #9a9a9a;
    --lettering-dark: #2b2a26;
  }
  * { box-sizing: border-box; margin: 0; padding: 0; }
  html, body {
    width: 1200px; height: 1000px; overflow: hidden;
    background: var(--canvas);
  }
  .canvas { position: relative; width: 1200px; height: 1000px; }

  .card {
    position: absolute; width: 760px;
    background: var(--paper);
    box-shadow: 0 3px 10px rgba(0,0,0,0.18);
    overflow: hidden;
  }
  .card--front { left: 97px; top: 85px; height: 420px; }
  .card--back { left: 343px; top: 522px; height: 410px; }

  .front__panel {
    position: absolute; left: 0; top: 0; width: 491px; height: 100%;
    background: var(--card-yellow);
  }

  .brand { position: absolute; color: var(--ink); font-family: "Open Sans", sans-serif; }
  .brand__name {
    display: flex; align-items: flex-start; gap: 14px;
    font-weight: 800; font-size: 60px; line-height: 0.92; letter-spacing: -2px;
  }
  .brand__dot {
    flex: none; width: 34px; height: 34px; margin-top: 8px;
    border-radius: 50%; background: var(--ink);
  }
  .brand__tagline {
    margin-top: 8px; font-weight: 600; font-size: 17px; letter-spacing: -0.3px;
  }
  .card--front .brand { left: 50px; top: 68px; }
  .card--back .brand { left: 62px; top: 250px; }

  .lettering { position: absolute; }
  .lettering--front {
    left: 522px; top: 55px; width: 200px; height: 145px;
    background: linear-gradient(160deg, #b4b4b4, var(--lettering-grey));
    border-radius: 6px; opacity: 0.55;
  }
  .lettering--back {
    left: 540px; top: 240px; width: 190px; height: 140px;
    background: linear-gradient(160deg, #4a473d, var(--lettering-dark));
    border-radius: 6px; opacity: 0.8;
  }

  .person {
    position: absolute; right: 297px; top: 262px; text-align: right;
    font-family: "Oswald", sans-serif;
  }
  .person__name { font-weight: 400; font-size: 27px; color: var(--ink); line-height: 1.1; }
  .person__role { font-weight: 300; font-size: 18px; color: var(--muted-grey); margin-top: 6px; }

  .address {
    position: absolute; left: 521px; top: 262px;
    font-family: "Oswald", sans-serif; font-weight: 300; font-style: normal;
    font-size: 22px; line-height: 32px; color: var(--ink);
  }

  .back__band {
    position: absolute; left: 0; top: 205px; width: 100%; height: 205px;
    background: var(--card-yellow);
  }
  .links {
    position: absolute; left: 105px; top: 45px; list-style: none;
    font-family: "Oswald", sans-serif; font-weight: 300; font-size: 21px; color: var(--ink);
  }
  .links__item { display: flex; align-items: center; gap: 18px; height: 31px; white-space: nowrap; }
  .links__icon {
    flex: none; width: 22px; height: 22px; border-radius: 50%; background: var(--ink);
    display: flex; align-items: center; justify-content: center;
  }
  .links__icon svg { width: 13px; height: 13px; fill: var(--card-yellow); }
</style>
</head>
<body>
<main class="canvas">

  <section class="card card--front" aria-label="Business card front">
    <div class="front__panel"></div>
    <div class="brand">
      <div class="brand__name"><span>Pluck &amp;<br>Lantern</span><span class="brand__dot"></span></div>
      <p class="brand__tagline">Bringing Every Chord to Life</p>
    </div>
    <div class="lettering lettering--front" role="img" aria-label="Hand-lettered slogan area"></div>
    <div class="person">
      <p class="person__name">Tobin Harrowfield</p>
      <p class="person__role">Director</p>
    </div>
    <address class="address">
      27 Kelawar Lane<br>
      Harbour Block B #05-12<br>
      Singapore 408761<br>
      Tel: +65 8104 5523
    </address>
  </section>

  <section class="card card--back" aria-label="Business card back">
    <ul class="links">
      <li class="links__item"><span class="links__icon"></span>www.pluckandlantern.com.sg/community</li>
      <li class="links__item"><span class="links__icon"></span>www.pluckandlantern.com.sg/videos/lessons-channel</li>
      <li class="links__item">
        <span class="links__icon"><svg viewBox="0 0 16 16"><path d="M8 1 1 7.5h2V15h4v-4h2v4h4V7.5h2z"/></svg></span>
        http://pluckandlantern.com.sg/
      </li>
      <li class="links__item">
        <span class="links__icon"><svg viewBox="0 0 16 16"><path d="M1 3h14v10H1z M2 4l6 5 6-5" fill="none" stroke="#f4d01c" stroke-width="1.6"/></svg></span>
        hello@pluckandlantern.com.sg
      </li>
    </ul>
    <div class="back__band"></div>
    <div class="brand">
      <div class="brand__name"><span>Pluck &amp;<br>Lantern</span><span class="brand__dot"></span></div>
      <p class="brand__tagline">Bringing Every Chord to Life</p>
    </div>
    <div class="lettering lettering--back" role="img" aria-label="Hand-lettered slogan area"></div>
  </section>

</main>
</body>
</html>
```